Book Cover on Entrepreneurship for Eye Doctors

Book Title: The Lens Practice Builder: How to launch with confidence
Author: Rufus Tembley, Optom, MBA, DBA, EIC
I need a Book Cover with the following descriptions:
Topic: the book topic is entrepreneurship knowledge for eye care professionals.
The book's audience: eye care professionals who you know as Opticians, who sell eyeglasses and sunglasses;
Optometrists, test eyes, fit contact lenses, and prescribe medication
Ophthalmologists, perform eye surgery
More about the audience:
1- Young eye care professionals who don’t know about entrepreneurship and those who are stuck in the 9-to-5 job;
2- This is the first book written on entrepreneurship with eye care professionals in mind.
3- Private practice owners the established business guys who are looking to grow their business;
4- Many eye care professionals are MBA holders they may have learned a little bit about entrepreneurship during their MBA studies.
Use the sample cover above and the suggestions that follow as a guide:
1- The cover should be very simple leaving an empty space somewhere to sign the book;
2- The Title and author name should use a modern font;
3- The cover should provide info about what's inside the book through illustrations, for example:
a- Gears: illustrating entrepreneur growth mindset (or anything more explicit)
b- Spectacles, sunglasses, lenses, eye drops, or any other eye care-related correction tools illustrating eye care (or anything more explicit)
c- Symbols illustrating ideas, opportunity, and profit, like money, charts, light bulbs, brain, and coins,...(or anything more explicit)
d- Entrepreneurship illustrated by Briefcase, tie, suit,... (or anything more explicit)

The rest is your creativity and imagination interplay.

Target Market(s)

Eye care professionals: Opticians, Optometrists, Ophthalmologists, Eye Care Administrators, Students in eye specialties.

Industry/Entity Type

eye care

Requirements
Must have
• 1- The cover should be very simple leaving an empty space somewhere to sign the book; 2- The Title and author name should use a modern font; 3- The cover should provide info about what's inside the book through illustrations, for example: a- Gears: illustrating entrepreneur growth mindset (or anything more explicit) b- Spectacles, sunglasses, lenses, eye drops, or any other eye care-related correction tools illustrating eye care (or anything more explicit) c- Symbols illustrating ideas, opportunity, and profit, like money, charts, light bulbs, brain, and coins,...(or anything more explicit) d- Entrepreneurship illustrated by Briefcase, tie, suit,... (or anything more explicit)

```html
<!DOCTYPE html>
<html lang="en">
<head>
<meta charset="utf-8">
<title>The Lens Practice Builder — Book Cover</title>
<link rel="stylesheet" href="https://fonts.googleapis.com/css2?family=Bebas+Neue&family=Oswald:wght@300;600&display=swap">
<style>
  :root {
    --stage-bg: #e4e4e4;
    --cover-blue: #0ba7cc;
    --frame-blue: #3aaee2;
    --title-white: #ffffff;
    --title-cream: #fdf4c0;
    --rule-gold: #f3e3a0;
    --photo-light: #eef3f8;
    --photo-mid: #c9dceb;
    --photo-deep: #9fbfd8;
    --desk-warm: #e8e2b4;
    --chart-glow: #ffffff;
  }
  * { margin: 0; padding: 0; box-sizing: border-box; }
  html, body {
    width: 1199px; height: 1200px; overflow: hidden;
    background: var(--stage-bg);
  }
  .stage {
    width: 1199px; height: 1200px;
    display: flex; align-items: center; justify-content: center;
  }
  .book-cover {
    position: relative;
    width: 780px; height: 1170px;
    background: var(--cover-blue);
    overflow: hidden;
  }
  .title {
    position: absolute; left: 0; right: 0; top: 46px;
    text-align: center;
    font-family: "Bebas Neue", "Oswald", sans-serif;
    font-weight: 400;
    line-height: 1;
    letter-spacing: 1px;
  }
  .title-line-one {
    display: block;
    color: var(--title-white);
    font-size: 112px;
  }
  .title-line-two {
    display: block;
    margin-top: 2px;
    color: var(--title-cream);
    font-size: 134px;
  }
  .subtitle {
    position: absolute; left: 147px; width: 486px; top: 339px; height: 59px;
    display: flex; align-items: center; justify-content: center;
    font-family: "Oswald", sans-serif;
    font-weight: 300;
    font-size: 27px;
    letter-spacing: 1.5px;
    color: var(--title-white);
    text-transform: uppercase;
  }
  .subtitle::before, .subtitle::after {
    content: ""; position: absolute; left: 0; right: 0; height: 1px;
    background: linear-gradient(90deg, transparent, var(--rule-gold) 50%, transparent);
    opacity: 0.9;
  }
  .subtitle::before { top: 0; }
  .subtitle::after { bottom: 0; }
  .lens-window {
    position: absolute; left: 0; top: 0;
    width: 780px; height: 1170px;
  }
  .growth-bar { fill: var(--chart-glow); fill-opacity: 0.28; stroke: var(--chart-glow); stroke-opacity: 0.85; stroke-width: 1.5; }
  .growth-line { fill: none; stroke: var(--chart-glow); stroke-width: 7; stroke-linecap: round; stroke-linejoin: round; opacity: 0.85; }
  .growth-point { fill: var(--chart-glow); }
  .author {
    position: absolute; left: 0; right: 0; top: 1066px;
    text-align: center;
    font-family: "Oswald", sans-serif;
    font-weight: 600;
    font-size: 35px;
    letter-spacing: 0.5px;
    color: var(--title-white);
    text-transform: uppercase;
  }
</style>
</head>
<body>
<main class="stage">
  <section class="book-cover">
    <h1 class="title">
      <span class="title-line-one">The Lens Practice</span>
      <span class="title-line-two">Builder</span>
    </h1>
    <p class="subtitle">How to launch with confidence</p>

    <svg class="lens-window" viewBox="0 0 780 1170" width="780" height="1170">
      <defs>
        <linearGradient id="photoTone" x1="0" y1="0" x2="0.6" y2="1">
          <stop offset="0" stop-color="var(--photo-mid)"/>
          <stop offset="0.5" stop-color="var(--photo-light)"/>
          <stop offset="0.8" stop-color="var(--photo-deep)"/>
          <stop offset="1" stop-color="var(--desk-warm)"/>
        </linearGradient>
        <clipPath id="lensClip">
          <path d="M0,576 Q390,314 780,576 L780,858 Q390,1158 0,858 Z"/>
        </clipPath>
      </defs>
      <path role="img" aria-label="Photo of eyeglasses on an optician's desk"
            d="M0,576 Q390,314 780,576 L780,858 Q390,1158 0,858 Z"
            fill="url(#photoTone)"/>

      <g class="growth-chart" clip-path="url(#lensClip)" role="img" aria-label="Rising growth chart">
        <rect class="growth-bar" x="134" y="870" width="64" height="160"/>
        <rect class="growth-bar" x="262" y="823" width="66" height="210"/>
        <rect class="growth-bar" x="404" y="713" width="68" height="320"/>
        <rect class="growth-bar" x="542" y="644" width="68" height="390"/>
        <polyline class="growth-line" points="78,887 210,800 330,745 420,700 500,668 538,580 560,520"/>
        <circle class="growth-point" cx="78" cy="887" r="6"/>
        <circle class="growth-point" cx="210" cy="800" r="6"/>
        <circle class="growth-point" cx="330" cy="745" r="6"/>
        <circle class="growth-point" cx="420" cy="700" r="6"/>
        <circle class="growth-point" cx="500" cy="668" r="6"/>
        <circle class="growth-point" cx="560" cy="520" r="8"/>
      </g>

      <path class="lens-frame" d="M0,576 Q390,314 780,576" fill="none" stroke="var(--frame-blue)" stroke-width="9"/>
      <path class="lens-frame" d="M780,858 Q390,1158 0,858" fill="none" stroke="var(--frame-blue)" stroke-width="9"/>
    </svg>

    <p class="author">Rufus Tembley, Optom, MBA, DBA, EIC</p>
  </section>
</main>
</body>
</html>
```